IT Company looking to market towards Dental Offices

I am looking for a full-color design. Using my existing logo. Must have High Res stock photos. The brochure needs to be full page edge to edge design single fold pamphlet style. Content provided. Please see the website in attached Word Doc for more content.

```html
<!DOCTYPE html>
<html lang="en">
<head>
<meta charset="utf-8">
<title>Bytewell Tech – Dental Practice Brochure</title>
<link rel="stylesheet" href="https://fonts.googleapis.com/css2?family=Open+Sans:ital,wght@0,300;0,400;0,600;0,700;0,800;1,400&display=swap">
<style>
  :root {
    --bg: #3b3b3b;
    --paper: #ffffff;
    --blue: #1f6fc5;
    --blue-bright: #2a86d6;
    --blue-deep: #1a4fa8;
    --navy: #1b2a6e;
    --navy-dark: #141f55;
    --ink: #4a4a4a;
    --photo-clinic-a: #e8f1fa;
    --photo-clinic-b: #b9d3ea;
    --photo-metal-a: #d9d9d9;
    --photo-metal-b: #7d7f82;
  }
  * { box-sizing: border-box; margin: 0; padding: 0; }
  html, body { width: 880px; height: 1200px; overflow: hidden; }
  body { background: var(--bg); font-family: "Open Sans", Arial, sans-serif; position: relative; }

  .spread { position: absolute; left: 30px; width: 820px; height: 580px; display: flex; box-shadow: 0 12px 30px rgba(0,0,0,.45); }
  .spread--outer { top: 15px; }
  .spread--inner { top: 605px; }
  .page { position: relative; width: 410px; height: 580px; overflow: hidden; background: var(--paper); }
  .page > svg { position: absolute; inset: 0; }
  .page .txt { position: absolute; }

  /* back cover */
  .back__intro { left: 30px; top: 82px; width: 200px; color: #fff; font-size: 10.5px; line-height: 1.42; }
  .back__cta { left: 34px; top: 505px; width: 350px; color: var(--ink); font-size: 10px; line-height: 1.45; }
  .back__cta strong { color: var(--navy); font-weight: 700; }

  /* front cover */
  .front__badge { left: 275px; top: 90px; width: 150px; color: #fff; text-align: center; line-height: 1.05; }
  .front__badge .lead { font-size: 11px; font-weight: 300; display: block; }
  .front__badge .big { font-size: 24px; font-weight: 800; display: block; letter-spacing: .5px; }
  .front__badge .mid { font-size: 11px; font-weight: 300; display: block; margin-top: 2px; }
  .front__badge .sub { font-size: 15px; font-weight: 800; display: block; margin-top: 3px; }
  .front__brand { left: 150px; top: 432px; display: flex; align-items: center; gap: 10px; }
  .front__brand .mark { width: 26px; height: 26px; border-radius: 50%; background: var(--navy); }
  .front__brand .name { font-size: 30px; font-weight: 800; color: var(--navy); letter-spacing: -.5px; }
  .front__web { left: 240px; top: 478px; font-size: 9.5px; color: var(--navy); display: flex; align-items: center; gap: 5px; }
  .front__web strong { font-weight: 700; }
  .front__web .dot { width: 9px; height: 9px; border-radius: 50%; background: var(--blue); }

  /* inner pages */
  .heading { color: #fff; font-size: 19px; font-weight: 300; letter-spacing: .5px; }
  .heading b { font-weight: 800; }
  .about { left: 40px; top: 40px; width: 215px; color: #fff; }
  .about p { font-size: 8.6px; line-height: 1.4; margin-top: 10px; text-align: justify; }
  .services { left: 24px; top: 398px; width: 370px; color: #fff; }
  .services .cols { display: flex; gap: 24px; margin-top: 12px; }
  .services ul { list-style: none; font-size: 8.4px; line-height: 1.55; }
  .services li::before { content: "✓"; margin-right: 5px; }
  .services li.group { font-weight: 700; text-transform: uppercase; font-size: 8px; }
  .services .col-b { margin-top: 30px; }

  .solutions { left: 236px; top: 45px; width: 170px; color: #fff; }
  .solutions ul { list-style: none; font-size: 8.4px; line-height: 1.5; margin-top: 8px; }
  .solutions li::before { content: "✓"; margin-right: 4px; }
  .ready { left: 40px; top: 360px; width: 345px; color: #fff; }
  .ready h2 { font-size: 17px; font-weight: 800; line-height: 1.15; letter-spacing: .5px; }
  .ready h3 { font-size: 8.5px; font-weight: 700; margin-top: 10px; }
  .ready ul { list-style: none; font-size: 8.4px; line-height: 1.5; margin-top: 4px; }
  .ready li::before { content: "✓"; margin-right: 4px; }
  .ready p { font-size: 9.5px; line-height: 1.45; margin-top: 10px; }
</style>
</head>
<body>

<!-- Outer spread: back cover + front cover -->
<section class="spread spread--outer">
  <article class="page page--back">
    <svg width="410" height="580" viewBox="0 0 410 580">
      <defs>
        <linearGradient id="clinic" x1="0" y1="0" x2="1" y2="1">
          <stop offset="0" stop-color="var(--photo-clinic-a)"/>
          <stop offset="1" stop-color="var(--photo-clinic-b)"/>
        </linearGradient>
      </defs>
      <rect x="0" y="0" width="410" height="480" fill="url(#clinic)" role="img" aria-label="Photo of a bright modern dental treatment room with patient chair"/>
      <rect x="0" y="480" width="410" height="100" fill="var(--paper)"/>
      <circle cx="120" cy="140" r="150" fill="var(--blue)" opacity=".92"/>
      <circle cx="330" cy="120" r="190" fill="none" stroke="var(--blue)" stroke-width=".7" opacity=".5"/>
      <circle cx="300" cy="225" r="28" fill="var(--blue-bright)" opacity=".85"/>
      <circle cx="330" cy="270" r="34" fill="var(--navy)" opacity=".9"/>
      <circle cx="380" cy="300" r="45" fill="var(--blue)" opacity=".85"/>
      <rect x="0" y="574" width="410" height="6" fill="var(--blue)"/>
    </svg>
    <p class="txt back__intro">Bytewell Tech offers proven expertise in Dental Practices. We have trained engineers that specialize in Dental practices. We can handle supporting you Practice Management Software to installing IOCs, Remote &amp; Sensors, Panos, X-rays, scanners, and pen pads. Being familiar with the Digital side of how your practice runs we will be able to predict and plan for your growth by providing the correct configurations and storage needs you will require. We know Dental!</p>
    <p class="txt back__cta">Get started today at <strong>www.molarvault.com</strong><br>We don't charge anything until we have confirmation that your Data has been successfully backed up on our encrypted servers.</p>
  </article>

  <article class="page page--front">
    <svg width="410" height="580" viewBox="0 0 410 580">
      <defs>
        <linearGradient id="vault" x1="0" y1="0" x2="1" y2="1">
          <stop offset="0" stop-color="var(--photo-metal-a)"/>
          <stop offset="1" stop-color="var(--photo-metal-b)"/>
        </linearGradient>
      </defs>
      <circle cx="215" cy="160" r="205" fill="none" stroke="var(--blue)" stroke-width=".7" opacity=".5"/>
      <circle cx="205" cy="150" r="185" fill="url(#vault)" role="img" aria-label="Photo of a round steel bank vault door set in stone"/>
      <circle cx="350" cy="155" r="100" fill="var(--blue-deep)" opacity=".95"/>
      <circle cx="340" cy="300" r="40" fill="var(--navy)" opacity=".85"/>
      <circle cx="300" cy="335" r="22" fill="var(--blue-bright)" opacity=".85"/>
      <rect x="0" y="574" width="410" height="6" fill="var(--blue)"/>
    </svg>
    <div class="txt front__badge">
      <span class="lead">Bytewell Tech</span>
      <span class="big">OFFERS</span>
      <span class="mid">proven expertise in</span>
      <span class="sub">DENTAL<br>PRACTICES</span>
    </div>
    <div class="txt front__brand"><span class="mark"></span><span class="name">Bytewell Tech</span></div>
    <div class="txt front__web"><span class="dot"></span>www.<strong>bytewelltech</strong>.com</div>
  </article>
</section>

<!-- Inner spread -->
<section class="spread spread--inner">
  <article class="page page--about">
    <svg width="410" height="580" viewBox="0 0 410 580">
      <defs>
        <linearGradient id="clinicGrey" x1="0" y1="0" x2="1" y2="1">
          <stop offset="0" stop-color="#eef0f3"/>
          <stop offset="1" stop-color="#b7bcc4"/>
        </linearGradient>
      </defs>
      <rect width="410" height="580" fill="url(#clinicGrey)" role="img" aria-label="Photo of a dental treatment chair in a clinic"/>
      <circle cx="150" cy="75" r="180" fill="var(--blue)"/>
      <circle cx="150" cy="75" r="192" fill="none" stroke="var(--blue)" stroke-width=".7" opacity=".6"/>
      <path d="M0 380 C120 330 300 330 410 370 L410 580 L0 580 Z" fill="var(--navy)"/>
    </svg>
    <div class="txt about">
      <h2 class="heading">ABOUT <b>US</b></h2>
      <p>Bytewell Tech offers a proven expertise in Dental Practices. We have trained engineers that specialize in Dental practice management solutions. We can handle supporting your Practice Management Software to installing IOCs, Remote &amp; Sensors, Panos, X-rays, scanners, pen pads, and more. Being familiar with Digital technology and how your practice runs we are able to predict and plan for your growth by providing the correct configurations the first time and implementing the proper storage solutions you will require. We know Dental!</p>
    </div>
    <div class="txt services">
      <h2 class="heading">OUR <b>SERVICES</b></h2>
      <div class="cols">
        <ul>
          <li class="group">Hardware Sales</li>
          <li>Servers</li>
          <li>Workstations</li>
          <li>Firewalls</li>
          <li>Routers</li>
          <li>Switches</li>
          <li>TVs &amp; Monitors</li>
          <li>Wireless Equipment</li>
          <li>Custom Check-in Workstations</li>
        </ul>
        <ul class="col-b">
          <li class="group">Infrastructure</li>
          <li>Data &amp; Voice Cable</li>
          <li>HDMI &amp; COAX Video Cable</li>
          <li>TV &amp; Dual Monitor Installation</li>
          <li>Mounting Hardware</li>
          <li>Wireless Installation</li>
          <li>Office Sound Solutions</li>
          <li>Custom Dental Cable</li>
          <li>Video Surveillance</li>
        </ul>
      </div>
    </div>
  </article>

  <article class="page page--solutions">
    <svg width="410" height="580" viewBox="0 0 410 580">
      <defs>
        <linearGradient id="servers" x1="0" y1="0" x2="1" y2="1">
          <stop offset="0" stop-color="#c9cbce"/>
          <stop offset="1" stop-color="#55585c"/>
        </linearGradient>
      </defs>
      <rect width="410" height="580" fill="var(--navy)"/>
      <circle cx="105" cy="190" r="140" fill="url(#servers)" role="img" aria-label="Photo of server racks in a data centre"/>
      <circle cx="105" cy="190" r="152" fill="none" stroke="#ffffff" stroke-width=".6" opacity=".4"/>
      <path d="M0 380 C90 300 260 290 410 330 L410 580 L0 580 Z" fill="var(--blue)"/>
      <path d="M0 380 C40 345 80 325 120 312 C60 345 30 380 0 420 Z" fill="var(--blue-bright)" opacity=".6"/>
    </svg>
    <div class="txt solutions">
      <h2 class="heading"><b>SOLUTIONS</b></h2>
      <ul>
        <li>Flat Rate Monthly Support</li>
        <li>Secure Backups with our MolarVault.com</li>
        <li>Secure Encrypted Emails &amp; X-Rays</li>
        <li>Practice Management Software Experts</li>
        <li>HIPAA Compliance</li>
        <li>Anti-Virus, Anti-Malware and Cyber Security</li>
        <li>Data Recovery</li>
        <li>Cloud Office Suites</li>
        <li>Phone VOIP &amp; SIP Trunks</li>
      </ul>
    </div>
    <div class="txt ready">
      <h2>READY TO MAKE<br>YOUR TECHNOLOGY WORK?</h2>
      <h3>How To Achieve Technology Bliss for Your Practice</h3>
      <ul>
        <li>Schedule a FREE Network &amp; Technology Evaluation</li>
        <li>Receive your Flat Rate Price and Technology Quote</li>
        <li>Sit back and let Bytewell Tech take care of everything.</li>
      </ul>
      <p>Don't let Technology Departments, Hardware Vendors and Practice Management vendors Point Fingers at each other. We collaborate everything and everyone for you, make one call to us and let us handle your technology.</p>
    </div>
  </article>
</section>

</body>
</html>
```